OpenHarbor Yoga Website Design

Business Logo - attached
5 pages being:
Home
About
Classes
Blog
Contact

Would like Scrolling webpage and yoga symbols to be used.

Must have's being:
Easy to navigate, Text needs to be able to be edited/updated, Enquire Now Links, More Information Links, be a secure site, SEO,

Please refer to attached document for the information for the body of the website.

Target Market(s)

Educators, Community Service, Health and Wellbeing, Mental Health

Industry/Entity Type

Yoga

Coding

Coded - Design and coding required

Number of Pages Required

5+ page

Font styles to use
Other font styles liked:
• Bella Bold BC

Colors
0094D4
00A9DD
6FCCEA
C7EBF8
E9F6FB
6B429C
8869AF
B7A5CE
E3DAEB
F3F0F8

Requirements
Must have
• Easy to navigate, Text needs to be able to be edited/updated, Enquire Now Links, More Information Links, be a secure site, SEO,
Nice to have
• Scrolling webpage, yoga symbols

```html
<!DOCTYPE html>
<html lang="en">
<head>
<meta charset="utf-8">
<title>OpenHarbor Yoga</title>
<link href="https://fonts.googleapis.com/css2?family=Poppins:wght@400;500;600&family=Kaushan+Script&display=swap" rel="stylesheet">
<style>
:root{
  --purple-deep:#5a2d8f;
  --purple:#6B429C;
  --purple-mid:#8869AF;
  --purple-soft:#B7A5CE;
  --lilac:#E3DAEB;
  --teal:#2a9fc6;
  --teal-bright:#1fb4d4;
  --sky:#6FCCEA;
  --ink:#111;
  --grey:#f3f3f3;
  --white:#fff;
}
*{margin:0;padding:0;box-sizing:border-box}
html,body{width:1200px;height:3712px;overflow:hidden}
body{position:relative;font-family:"Poppins",sans-serif;color:var(--ink);background:var(--white)}
.abs{position:absolute}
.script{font-family:"Kaushan Script",cursive;font-weight:400}

/* hero */
.hero-bg{left:0;top:0;width:1200px;height:640px;background:linear-gradient(180deg,#e9e4de 0%,#ddd6cf 40%,#b7b19c 75%,#8f8a6a 100%)}
.band{left:0;top:640px;width:1200px;height:372px;background:linear-gradient(180deg,var(--purple-deep) 0%,#5a4aa0 35%,var(--teal-bright) 100%)}
.brand{left:100px;top:60px;display:flex;align-items:center;gap:10px;color:var(--purple-mid);font-weight:600;font-size:22px}
.brand-dot{width:22px;height:22px;border-radius:50%;background:var(--purple-mid)}
.nav{left:486px;top:58px;display:flex;gap:38px;font-size:16px;font-weight:500}
.nav a{color:var(--ink);text-decoration:none}
.login{left:980px;top:47px;width:115px;height:40px;border-radius:5px;background:linear-gradient(90deg,var(--purple-deep),var(--teal-bright));color:var(--white);font-size:16px;font-weight:500;display:flex;align-items:center;justify-content:center}
.hero-title{left:104px;top:248px;font-size:46px;line-height:72px}
.hero-title .em{color:#6a2ed6;font-size:52px}
.hero-text{left:104px;top:392px;width:380px;font-size:12.5px;line-height:24.5px}
.hero-photo{left:648px;top:160px;width:547px;height:560px;border-radius:260px 260px 30px 30px;background:linear-gradient(180deg,#c9b1ef 0%,#d8cfc6 55%,#9b8a73 100%)}
.band-text{left:104px;top:776px;width:1000px;color:var(--white);font-size:17.5px;line-height:37px}

/* about */
.about-photo{left:216px;top:922px;width:224px;height:638px;border-radius:110px 110px 12px 12px;background:linear-gradient(180deg,#d6e2ea 0%,#b9c3cb 60%,#8c959d 100%)}
.about-title{left:641px;top:1082px;font-size:44px}
.about-title span{color:#6a2ed6}
.about-sub{left:641px;top:1152px;font-size:17px;color:var(--teal)}
.about-text{left:641px;top:1184px;width:455px;font-size:12px;line-height:22.5px}
.about-text p{margin-bottom:8px}
.btn{left:641px;top:1436px;width:114px;height:40px;border-radius:6px;background:linear-gradient(90deg,var(--purple-deep),var(--teal-bright));color:var(--white);font-size:16px;font-weight:500;display:flex;align-items:center;justify-content:center}

/* gallery */
.gallery-band{left:0;top:1902px;width:1200px;height:132px;background:var(--grey)}
.tile{width:223px;background-clip:content-box}
.arrows{left:574px;top:1931px;display:flex;gap:16px}

/* benefits */
.ben-title{left:0;top:2105px;width:1200px;text-align:center;font-size:44px}
.ben-title .sm{font-size:30px;color:var(--purple)}
.ben-title .em{color:var(--purple)}
.ben-photo{left:310px;top:2348px;width:612px;height:490px;border-radius:300px 300px 0 0;background:linear-gradient(180deg,#c9b9e4 0%,#b3c6e6 55%,#86d0ea 100%)}
.teal{left:0;top:2838px;width:1200px;height:472px;background:var(--teal)}
.rings{left:0;top:2190px}
.icon{width:80px;height:80px;border-radius:50%;background:radial-gradient(circle at 40% 35%,#8a4fd0,#4a1f7e);border:3px solid #fff3;display:flex;align-items:center;justify-content:center}
.col{color:var(--white)}
.col h3{font-family:"Kaushan Script",cursive;font-weight:400;font-size:25px;margin-bottom:10px}
.col li{list-style:none;font-size:10.5px;line-height:21.5px}
.col li::before{content:"• "}

/* footer */
.f-brand{left:137px;top:3470px;display:flex;align-items:center;gap:10px;color:var(--purple-soft);font-weight:600;font-size:24px}
.f-col h4{font-family:"Kaushan Script",cursive;font-weight:400;font-size:22px;color:var(--purple);margin-bottom:14px}
.f-col a{display:block;font-size:12px;color:var(--ink);text-decoration:none;line-height:29px}
.email{left:797px;top:3446px;width:264px;border-bottom:1px solid var(--purple);font-size:12px;padding-bottom:6px;display:flex;justify-content:space-between;align-items:center}
.socials{left:797px;top:3486px;display:flex;gap:8px}
.socials span{width:16px;height:16px;border-radius:50%;background:var(--purple-mid)}
.rule{left:104px;top:3652px;width:991px;height:1px;background:var(--purple)}
.copy{left:0;top:3672px;width:1200px;text-align:center;font-size:11.5px}
</style>
</head>
<body>

<div class="abs hero-bg" role="img" aria-label="Misty mountain and forest landscape background"></div>
<div class="abs band"></div>

<div class="abs brand"><span class="brand-dot"></span>OpenHarbor Yoga</div>
<nav class="abs nav"><a href="#">Home</a><a href="#">About</a><a href="#">Classes</a><a href="#">Blog</a><a href="#">Contact</a></nav>
<a class="abs login">Log In</a>

<h1 class="abs hero-title script">Welcome to<br><span class="em">OpenHarbor Yoga...</span></h1>
<p class="abs hero-text">OpenHarbor Yoga believe that you are never too young to benefit from and fall in love with yoga. My aim is to EMPOWER kids and teens to thrive by teaching life skills in Yoga, Mindfulness and Breathing techniques to deal with daily challenges and big emotions.</p>
<div class="abs hero-photo" role="img" aria-label="Woman meditating cross-legged on a stone slab"></div>

<p class="abs band-text">OpenHarbor Yoga gives kids an opportunity to enjoy and experience yoga for themselves and primarily focuses on programs for Schools, Pre Schools and Early Learning Centres, Private Classes, Sporting Clubs, Martial Arts Schools, Scout Groups and Occupational Therapy Centres just to name a few. All classes are age appropriate and encourage children's natural drive to learn, move, and be creative</p>

<div class="abs about-photo" role="img" aria-label="Woman in tree pose with arms raised overhead"></div>
<h2 class="abs about-title script">About <span>OpenHarbor Yoga!</span></h2>
<p class="abs about-sub script">Hi and welcome to OpenHarbor Yoga!</p>
<div class="abs about-text">
  <p>My name is Clara, and I am the creator &amp; facilitator of OpenHarbor Yoga.</p>
  <p>With the increasing numbers of youth mental health, I have started OpenHarbor Yoga wanting to assist children and teens with their mental health for life, with the magic of yoga.I had always wanted to teach children, but had never found the right platform to do so... That was until I found yoga!</p>
  <p>I genuinely believe the practice of yoga and mindfulness especially at a young age can offer life-long tools to kids and teens such as dealing with their emotions, developing resilience, self-awareness, respect and confidence in a positive and fun environment.</p>
</div>
<a class="abs btn">Read More</a>

<div class="abs gallery-band"></div>
<div class="abs tile" style="left:9px;top:1613px;height:281px;background:linear-gradient(180deg,#e8e6e2,#9a9a98)" role="img" aria-label="Man meditating on a mat indoors"></div>
<div class="abs tile" style="left:249px;top:1570px;height:281px;background:linear-gradient(180deg,#eceef0,#b5b9bd)" role="img" aria-label="Woman in tree pose against a white wall"></div>
<div class="abs tile" style="left:490px;top:1613px;height:281px;background:linear-gradient(180deg,#7c9a3c,#3f6a22)" role="img" aria-label="Woman in a backbend on grass in a park"></div>
<div class="abs tile" style="left:729px;top:1548px;height:281px;background:linear-gradient(180deg,#3a9fb8,#f0a250)" role="img" aria-label="Silhouette in warrior pose at sunset"></div>
<div class="abs tile" style="left:970px;top:1613px;height:281px;background:linear-gradient(180deg,#eeeae6,#c8c3bd)" role="img" aria-label="Woman in green outfit in tree pose"></div>
<div class="abs arrows">
  <svg width="18" height="18" viewBox="0 0 18 18"><circle cx="9" cy="9" r="8" fill="none" stroke="#2a9fc6" stroke-width="2"/><path d="M12 9H6M9 6L6 9l3 3" fill="none" stroke="#2a9fc6" stroke-width="2"/></svg>
  <svg width="18" height="18" viewBox="0 0 18 18"><circle cx="9" cy="9" r="8" fill="none" stroke="#111" stroke-width="2"/><path d="M6 9h6M9 6l3 3-3 3" fill="none" stroke="#111" stroke-width="2"/></svg>
</div>

<h2 class="abs ben-title script">Benefits <span class="sm">of</span> <span class="em">Yoga...</span></h2>
<div class="abs ben-photo" role="img" aria-label="Woman in warrior two pose in front of a mandala"></div>
<div class="abs teal"></div>
<svg class="abs rings" width="1200" height="880" viewBox="0 2190 1200 880">
  <circle cx="590" cy="2622" r="410" fill="none" stroke="#4a1f7e" stroke-width="2"/>
  <circle cx="590" cy="2622" r="353" fill="none" stroke="#8869AF" stroke-width="1.5"/>
  <circle cx="590" cy="2622" r="274" fill="none" stroke="#B7A5CE" stroke-width="1.5"/>
</svg>

<div class="abs icon" style="left:237px;top:2855px"><svg width="40" height="40" viewBox="0 0 40 40" fill="none" stroke="#fff" stroke-width="1.5"><circle cx="20" cy="8" r="4"/><path d="M20 12v14M10 16h20M20 26l-6 10M20 26l6 10"/></svg></div>
<div class="abs icon" style="left:565px;top:2927px"><svg width="40" height="40" viewBox="0 0 40 40" fill="none" stroke="#fff" stroke-width="1.5"><ellipse cx="20" cy="20" rx="13" ry="10"/><path d="M20 10v20M12 16c4 2 4 6 0 8M28 16c-4 2-4 6 0 8"/></svg></div>
<div class="abs icon" style="left:899px;top:2812px"><svg width="40" height="40" viewBox="0 0 40 40" fill="none" stroke="#fff" stroke-width="1.5"><path d="M20 8c5 6 5 14 0 20-5-6-5-14 0-20zM20 28c-6-2-11-7-12-14 6 1 10 6 12 14zM20 28c6-2 11-7 12-14-6 1-10 6-12 14zM8 30h24"/></svg></div>

<div class="abs col" style="left:112px;top:2948px;width:270px">
  <h3>Healthy Bodies:</h3>
  <ul>
    <li>Develops strong, flexible and healthy bodies</li>
    <li>Promotes spinal alignment and good posture</li>
    <li>Builds energy and stamina</li>
    <li>Improves internal physical function - organs, digestion, elimination, circulation, and blood flow.</li>
    <li>Helps breathing and lung capacity</li>
    <li>Teaches the enjoyment of movement</li>
    <li>Works the 'whole' body</li>
  </ul>
</div>
<div class="abs col" style="left:537px;top:3056px;width:290px">
  <h3>Healthy Minds</h3>
  <ul>
    <li>Cultivates confidence and self-esteem</li>
    <li>Develops concentration and attention</li>
    <li>Clears the mind for better clarity and decisionmaking</li>
    <li>Helps relax and sleep better</li>
    <li>Calms the nervous system</li>
    <li>Learns to cope with stressful situations</li>
    <li>Balances emotions</li>
  </ul>
</div>
<div class="abs col" style="left:907px;top:2908px;width:260px">
  <h3>Healthy Spirits</h3>
  <ul>
    <li>Fosters creativity, expression and imagination</li>
    <li>Cultivates kindness to themselves and others</li>
    <li>Cultivates respect for self and others</li>
    <li>Builds balance and inner quiet</li>
    <li>Builds inner strength and resilience</li>
    <li>Teaches self-awareness</li>
    <li>Focuses on positive self-talk</li>
  </ul>
</div>

<div class="abs f-brand"><span class="brand-dot" style="background:var(--purple-soft)"></span>OpenHarbor Yoga</div>
<div class="abs f-col" style="left:471px;top:3398px"><h4>Quick Links</h4><a href="#">Home</a><a href="#">About</a><a href="#">Classes</a><a href="#">Blog</a><a href="#">Contact</a></div>
<div class="abs f-col" style="left:629px;top:3398px"><h4>Help Links</h4><a href="#">Enquire Now</a><a href="#">More Information</a></div>
<div class="abs f-col" style="left:797px;top:3398px"><h4>Newsletter</h4></div>
<div class="abs email"><span>&#9993; Enter Email</span><svg width="12" height="12" viewBox="0 0 12 12"><path d="M1 6l10-5-3 10-2-4z" fill="#2a9fc6"/></svg></div>
<div class="abs socials"><span></span><span></span><span></span></div>
<div class="abs rule"></div>
<p class="abs copy">@ 2023 OpenHarbor Yoga | All Rights Reserved | Privacy Policy | Terms and Conditions</p>

</body>
</html>
```